Business card

We need a business card design for our company based in Auckland , New Zealand called 'Ridge + Studio Ltd'. We provide architectural services. We would like to see designs that use the max. three colours (such as white, black, grey) The final design should communicate financial safety and growth."
Also I will provide our company logo. I would like to the logo to be embeded onto our business card.

Target Market(s)

new residential house, alteration & addition & light commericila design & drafting service

Industry/Entity Type

Architecture

Contact Information for Business Card

Company name: ridge + studio Ltd.
Name: Mark Delford
Job title: architectural designer & Design LBP
email address: mark@rplusd.co.nz
mobile number: 02 5163 2290
web site: www.rplusd.co.nz

Requirements
Must have
• My project must have..
• - embeded logo (attached company logo)
• I don't have a bigger version for our company logo, but I have one old one, so you can remove the word from it)
• - insert the attached small BKTW logo & LBP logo
• - creative, simple and clear business card.
• - Max. three colours
Nice to have
• - Here are the samples I would like to share with you: http://www.plimvora.com/blog/minimalistic-business-card-designs/
• I would like to have my business card like one of the creation.
Should not have
• TBA

```html
<!DOCTYPE html>
<html lang="en">
<head>
<meta charset="utf-8">
<title>Ridge + Studio Ltd. — Business Card</title>
<link rel="stylesheet" href="https://fonts.googleapis.com/css2?family=Open+Sans:wght@400;600&family=Roboto:wght@500&display=swap">
<style>
  :root {
    --ink: #0c0c0c;
    --paper: #ffffff;
    --grey: #c9c9c9;
    --stage: #e6e6e6;
    --text-soft: #e8e8e8;
  }
  * { box-sizing: border-box; margin: 0; padding: 0; }
  html, body { width: 1200px; height: 900px; overflow: hidden; }
  body {
    background: var(--stage);
    display: flex;
    align-items: center;
    justify-content: center;
    gap: 40px;
    font-family: "Open Sans", Arial, sans-serif;
  }
  .card {
    position: relative;
    width: 540px;
    height: 330px;
    background: var(--ink);
    overflow: hidden;
    box-shadow: 0 6px 18px rgba(0,0,0,0.18);
  }
  /* Back side */
  .card-back .company-title {
    position: absolute;
    top: 70px;
    left: 0;
    right: 0;
    text-align: center;
    font-family: "Roboto", Arial, sans-serif;
    font-weight: 500;
    font-size: 30px;
    color: var(--paper);
    letter-spacing: 0.2px;
  }
  .card-back .badges {
    position: absolute;
    top: 150px;
    left: 0;
    right: 0;
    display: flex;
    justify-content: center;
    align-items: center;
    gap: 28px;
  }
  .badge-member {
    width: 130px;
    height: 62px;
    background: var(--paper);
    border-radius: 4px;
  }
  .badge-licence {
    width: 108px;
    height: 108px;
    border-radius: 50%;
    background: var(--paper);
    border: 6px solid var(--grey);
  }
  /* Front side */
  .card-front .wave { position: absolute; inset: 0; }
  .holder {
    position: absolute;
    top: 58px;
    left: 50px;
    color: var(--paper);
  }
  .holder-name { font-weight: 600; font-size: 19px; line-height: 1.2; }
  .holder-role { font-size: 15px; color: var(--text-soft); line-height: 1.3; }
  .brand {
    position: absolute;
    top: 46px;
    right: 40px;
    display: flex;
    flex-direction: column;
    align-items: center;
    gap: 12px;
  }
  .brand-dot {
    width: 70px;
    height: 70px;
    border-radius: 50%;
    background: var(--paper);
  }
  .brand-name { font-size: 17px; color: var(--paper); }
  .contacts {
    position: absolute;
    left: 52px;
    top: 174px;
    list-style: none;
    color: var(--paper);
    font-size: 15px;
    line-height: 24px;
  }
  .contacts li { display: flex; align-items: center; gap: 10px; }
  .contacts svg { width: 13px; height: 13px; fill: var(--paper); flex: none; }
</style>
</head>
<body>

  <section class="card card-back" aria-label="Business card, back">
    <h1 class="company-title">Ridge + Studio Ltd.</h1>
    <div class="badges">
      <div class="badge-member" role="img" aria-label="BKTW professional member badge"></div>
      <div class="badge-licence" role="img" aria-label="Licensed practitioner badge"></div>
    </div>
  </section>

  <section class="card card-front" aria-label="Business card, front">
    <svg class="wave" viewBox="0 0 540 330" preserveAspectRatio="none" aria-hidden="true">
      <path d="M0,298 C150,294 245,260 325,218 C402,178 466,168 540,170 L540,330 L0,330 Z" fill="var(--grey)"/>
      <path d="M0,308 C150,304 250,270 330,228 C405,190 468,180 540,182" fill="none" stroke="var(--ink)" stroke-width="3"/>
      <path d="M0,315 C150,311 254,277 333,236 C408,198 470,188 540,190 L540,330 L0,330 Z" fill="var(--paper)"/>
    </svg>

    <div class="holder">
      <p class="holder-name">Mark Delford</p>
      <p class="holder-role">Architectural designer &amp; Design LBP</p>
    </div>

    <div class="brand">
      <span class="brand-dot" aria-hidden="true"></span>
      <span class="brand-name">Ridge + Studio Ltd.</span>
    </div>

    <ul class="contacts">
      <li>
        <svg viewBox="0 0 16 16" aria-hidden="true"><path d="M3.6 1 6 3.4 4.6 5.6c.9 2 2.6 3.7 4.7 4.7l2.2-1.4L14 11.4 12.6 14C6.8 14 2 9.2 2 3.4Z"/></svg>
        02 5163 2290
      </li>
      <li>
        <svg viewBox="0 0 16 16" aria-hidden="true"><path d="M1 3h14v10H1Z M2.5 4.5 8 9l5.5-4.5" fill="none" stroke="#fff" stroke-width="1.5"/></svg>
        mark@rplusd.co.nz
      </li>
      <li>
        <svg viewBox="0 0 16 16" aria-hidden="true"><circle cx="8" cy="8" r="7"/></svg>
        www.rplusd.co.nz
      </li>
    </ul>
  </section>

</body>
</html>
```